Website Homepage for Gulfward Crestline Labs

Website is a white label new branding of this product:
https://www.roofbrillo.example

Looking for home page / landing page design.

The focus should be on its characteristics that showcase its ability to protect your roof from hurricanes and weather. Focus is only on the roof use case.

Helps restore original color
Bonds shingle granules
Penetrates and rejuvenates
Extend your roofs life
Prevents mold, mildew and moss growth
FrostGuard Colors are heat reflective and UV resistance
Environmentally Friendly
Added flexibility
Added Impact Resistance
Added Wind Resistance
Heat reflective
Reflect harmful UV rays
Reduce energy consumption
Extend the life of the shingle
Stop mold, mildew and algae from growing again!
Built it mildicide, moldicide, and algaecide.

Some other consideration marketing ideas to portray:

Roof replacement alternative with $0 down financing

Don’t replace, rejuvenate!

Stop! Before replacing your roof look at this solution…. With our advanced technology spray and seal coatings you can have a rejuvenated roof that is better than a new one! At a fraction of the cost!

Repel wind, repel water and repel impact. Make your roof stronger than ever.

Is your roof ready for hurricane season? What if there was a simple 1 day application coating that could help you to strengthen your roof against wind, rain and impact?

Self insured home? Protect your roof with our rejuvenating roof coatings that extend the life of your roof by 15+ years.

Have you recently installed a roof? Don’t wait for the next hurricane to damage it. Protect it today with our sealant coatings that repel wind, water and impact!

Ready for a new roof but don’t have the budget. Use our colored coatings that not only make your roof new again, but can also recolor it!

The sun is damaging your roof every day! Our coatings protect it from UV damage as well as water, wind, and impact!

Have a tile or clay roof? Tired of algae, mold and mildew growing on your roof? We will clean your roof and prevent regrowth in the future with our coatings!

Industry/Entity Type

Construction

Number of Pages Required

1 page

Font styles to use
Sans Serif

Colors
0054AA
0677BA
7BADD7
CADEEF
E8F1F8
0094D4
00A9DD
6FCCEA
C7EBF8
E9F6FB

Requirements
Nice to have
• Modern blue / grey / black color scheme. Not a lot of white space.

```html
<!DOCTYPE html>
<html lang="en">
<head>
<meta charset="utf-8">
<title>Tidewell Sealer — Don't Replace Your Roof</title>
<link href="https://fonts.googleapis.com/css2?family=Open+Sans:wght@600;700;800&family=Arimo:wght@400;700&display=swap" rel="stylesheet">
<style>
:root{
  --navy-900:#020a1c;
  --navy-800:#04112b;
  --navy-700:#081a3d;
  --card:#071634;
  --blue:#0677BA;
  --blue-bright:#0a7fd6;
  --blue-deep:#0054AA;
  --sky:#7BADD7;
  --ice:#E8F1F8;
  --white:#ffffff;
  --muted:#c9d3e3;
  --star:#e8552a;
  --field-border:#3a4660;
}
*{box-sizing:border-box;margin:0;padding:0}
html,body{width:1200px;height:4815px;overflow:hidden}
body{position:relative;background:linear-gradient(180deg,var(--navy-800) 0%,var(--navy-900) 40%,var(--navy-800) 70%,var(--navy-900) 100%);color:var(--white);font-family:"Arimo",Arial,sans-serif}
.abs{position:absolute}
.heading{font-family:"Open Sans",Arial,sans-serif;font-weight:800;color:var(--white)}
.btn{position:absolute;display:flex;align-items:center;justify-content:center;gap:8px;background:var(--blue-bright);color:var(--white);border-radius:22px;font-family:"Arimo",Arial,sans-serif;font-weight:700;font-size:13px;letter-spacing:.3px}
.btn svg{width:12px;height:12px}
/* hero */
.hero-photo{position:absolute;left:0;top:0;width:1200px;height:626px;background:radial-gradient(ellipse at 560px 80px,#2b4f9a 0%,#0d1d44 30%,transparent 55%),linear-gradient(180deg,#0a1534 0%,#1b2236 38%,#6a5a42 60%,#b99a66 72%,#3f4a3a 100%)}
.nav{position:absolute;top:38px;left:452px;display:flex;gap:0;font-size:13px;font-family:"Arimo",Arial,sans-serif}
.nav span{position:absolute;white-space:nowrap}
.logo{position:absolute;font-family:"Open Sans",Arial,sans-serif;font-weight:800;color:var(--white);display:flex;align-items:center;gap:10px}
.logo i{display:block;width:16px;height:16px;border-radius:50%;background:var(--blue-bright)}
.eyebrow{left:0;width:1200px;text-align:center;top:638px;font-size:38px;color:var(--blue-bright);font-family:"Open Sans",Arial,sans-serif;font-weight:800;letter-spacing:1px}
.hero-title{left:0;width:1200px;text-align:center;top:678px;font-size:86px;line-height:100px;letter-spacing:1px}
.tagline{left:0;width:1200px;top:784px;display:flex;justify-content:center;align-items:center;gap:22px;font-family:"Open Sans",Arial,sans-serif;font-weight:700;font-size:24px;letter-spacing:1px}
.tagline b{display:block;width:86px;height:4px;background:var(--blue-bright);border-radius:2px}
/* services */
.service-card{position:absolute;top:963px;width:265px;height:215px;border:3px solid #e9eef6;border-radius:24px}
.service-label{position:absolute;top:1206px;width:265px;text-align:center;font-family:"Open Sans",Arial,sans-serif;font-weight:700;font-size:13px;letter-spacing:.3px}
.arrow{position:absolute;width:20px;height:20px}
/* about */
.photo{position:absolute}
.stat-box{position:absolute;background:var(--navy-700);border:1px solid #2a3a60;text-align:center;color:var(--white)}
.section-title{position:absolute;font-size:54px;font-family:"Open Sans",Arial,sans-serif;font-weight:800}
.body-copy{position:absolute;font-size:13px;line-height:26px;color:var(--muted);text-align:justify}
.sub-title{position:absolute;font-family:"Open Sans",Arial,sans-serif;font-weight:700;font-size:22px}
.benefit{position:absolute;display:flex;align-items:center;gap:12px;font-weight:700;font-size:14px}
.benefit svg{width:14px;height:14px}
/* testimonials */
.testimonial{position:absolute;top:2747px;width:274px;height:234px;background:var(--card);border-radius:22px}
.testimonial .avatar{position:absolute;left:22px;top:24px;width:52px;height:52px;border-radius:50%;background:linear-gradient(135deg,#8a7a6a,#4b4a52)}
.testimonial .name{position:absolute;left:90px;top:40px;font-weight:700;font-size:16px}
.testimonial .stars{position:absolute;left:178px;top:38px;color:var(--star);font-size:15px;letter-spacing:1px}
.testimonial p{position:absolute;left:28px;top:98px;width:220px;font-size:13px;line-height:26px;color:var(--muted)}
/* tests */
.tab{position:absolute;top:3265px;height:49px;border-radius:25px;background:var(--white);color:#0b1530;display:flex;align-items:center;justify-content:center;font-weight:700;font-size:12px;letter-spacing:.2px}
.tab.active{background:var(--navy-700);color:var(--white)}
/* form */
.field{position:absolute;height:62px;border:1px solid var(--field-border);border-radius:26px;background:var(--navy-900);padding-left:34px;display:flex;align-items:center;font-size:13px;font-weight:700;letter-spacing:.3px}
/* footer */
.foot-head{position:absolute;top:4503px;font-weight:700;font-size:12px;letter-spacing:.3px}
.foot-link{position:absolute;font-size:13px;color:var(--muted)}
.social{position:absolute;top:4743px;width:30px;height:30px;border-radius:50%;background:var(--blue-bright)}
</style>
</head>
<body>

<!-- Hero -->
<div class="hero-photo" role="img" aria-label="Lit stone house at night under a stormy sky with a lightning bolt"></div>
<svg class="abs" style="left:0;top:500px" width="1200" height="140" viewBox="0 0 1200 140">
  <polygon points="0,126 596,30 1200,126 1200,140 0,140" fill="#04112b"/>
  <polyline points="0,126 596,30 1200,126" fill="none" stroke="#0a7fd6" stroke-width="4"/>
  <polyline points="0,118 596,22 1200,118" fill="none" stroke="#ffffff" stroke-width="2" opacity=".6"/>
</svg>

<div class="logo" style="left:130px;top:48px;font-size:24px"><i></i>Tidewell Sealer</div>

<nav class="nav" aria-label="Main">
  <span style="left:0">Home</span>
  <span style="left:78px">About</span>
  <span style="left:155px">Services</span>
  <span style="left:249px">Roof Sealers ▾</span>
  <span style="left:376px">Video</span>
  <span style="left:453px">Standards Testing ▾</span>
  <span style="left:589px">More</span>
</nav>

<div class="abs eyebrow">DON'T REPLACE</div>
<h1 class="abs heading hero-title">YOUR ROOF</h1>
<div class="abs tagline"><b></b>RESTORE • PROTECT • PRESERVE<b></b></div>
<div class="btn" style="left:499px;top:848px;width:170px;height:42px">GET A QUOTE <svg viewBox="0 0 12 12"><circle cx="6" cy="6" r="6" fill="#fff"/><path d="M5 3.5 7.5 6 5 8.5" stroke="#0a7fd6" stroke-width="1.6" fill="none"/></svg></div>

<!-- Services carousel -->
<svg class="arrow" style="left:67px;top:1063px" viewBox="0 0 20 20"><path d="M13 3 6 10l7 7" stroke="#fff" stroke-width="2.2" fill="none"/></svg>
<svg class="arrow" style="left:1111px;top:1063px" viewBox="0 0 20 20"><path d="M7 3l7 7-7 7" stroke="#fff" stroke-width="2.2" fill="none"/></svg>
<div class="service-card" style="left:159px;background:linear-gradient(160deg,#7d8a96,#2a2f36 60%,#15181d)" role="img" aria-label="Roof coating being rolled onto a flat roof"></div>
<div class="service-card" style="left:465px;background:linear-gradient(160deg,#9fc4e6,#e1772f 45%,#a9441a)" role="img" aria-label="Orange ceramic roof tiles against blue sky"></div>
<div class="service-card" style="left:776px;background:linear-gradient(160deg,#6c7780,#3a4248 60%,#bcd3e4)" role="img" aria-label="Grey clay tile roof with a skylight window"></div>
<div class="service-label" style="left:159px">ROOF COATING</div>
<div class="service-label" style="left:465px">SEAL FOR CERAMIC TILE</div>
<div class="service-label" style="left:776px">FROSTGUARD FOR CLAY TILE</div>

<!-- About -->
<div class="photo" style="left:107px;top:1346px;width:491px;height:510px;background:linear-gradient(150deg,#e9ecef 0%,#c8cbd0 35%,#6d6f74 75%,#4a4c50 100%)" role="img" aria-label="Roofer in a hard hat installing asphalt shingles"></div>
<div class="stat-box" style="left:432px;top:1346px;width:166px;height:175px">
  <div style="margin-top:34px;font-family:'Open Sans',Arial,sans-serif;font-weight:600;font-size:36px">15+ <span style="font-size:15px">YRS</span></div>
  <div style="font-size:15px;line-height:30px;margin-top:6px">EXTEND THE LIFE<br>OF YOUR ROOF</div>
</div>
<h2 class="section-title" style="left:650px;top:1372px">About Us</h2>
<p class="body-copy" style="left:650px;top:1460px;width:444px">Tidewell is a proprietary rejuvenating clear sealer developed to protect and preserve your asphalt shingles.Preventing the expensive cost of re-roofing. Providing an exclusive Consumer First Protection Warranty for 10 years.</p>
<h3 class="sub-title" style="left:650px;top:1581px">Environmentally Friendly</h3>
<p class="body-copy" style="left:650px;top:1628px;width:444px">Helps prevent shingle waste in Americas landfills. Tons of shingles are dumped into our landfills annually.  Granules are not biodegradable and some granules are coated with a ceramic paint which is harmful to our environment.  Tidewell is warranted to bond granules to the shingle.</p>
<div class="btn" style="left:650px;top:1757px;width:169px;height:42px">LEARN MORE <svg viewBox="0 0 12 12"><circle cx="6" cy="6" r="6" fill="#fff"/><path d="M5 3.5 7.5 6 5 8.5" stroke="#0a7fd6" stroke-width="1.6" fill="none"/></svg></div>

<!-- Benefits -->
<h2 class="section-title" style="left:107px;top:2046px">Our Benefits</h2>
<p class="body-copy" style="left:107px;top:2131px;width:444px">Tidewell is a proprietary rejuvenating clear sealer developed to protect and preserve your asphalt shingles. Preventing the expensive cost of re-roofing. Providing an exclusive Consumer First Protection Warranty for 10 years. Extend your roof life up to 30 years.</p>
<div class="benefit" style="left:107px;top:2255px"><svg viewBox="0 0 14 14"><circle cx="7" cy="7" r="7" fill="#fff"/><path d="M6 4 9 7 6 10" stroke="#04112b" stroke-width="1.8" fill="none"/></svg>Helps restore original color</div>
<div class="benefit" style="left:350px;top:2255px"><svg viewBox="0 0 14 14"><circle cx="7" cy="7" r="7" fill="#fff"/><path d="M6 4 9 7 6 10" stroke="#04112b" stroke-width="1.8" fill="none"/></svg>Added flexibility</div>
<div class="benefit" style="left:107px;top:2295px"><svg viewBox="0 0 14 14"><circle cx="7" cy="7" r="7" fill="#fff"/><path d="M6 4 9 7 6 10" stroke="#04112b" stroke-width="1.8" fill="none"/></svg>Bonds shingle granules</div>
<div class="benefit" style="left:350px;top:2295px"><svg viewBox="0 0 14 14"><circle cx="7" cy="7" r="7" fill="#fff"/><path d="M6 4 9 7 6 10" stroke="#04112b" stroke-width="1.8" fill="none"/></svg>Impact Resistance</div>
<div class="benefit" style="left:107px;top:2338px"><svg viewBox="0 0 14 14"><circle cx="7" cy="7" r="7" fill="#fff"/><path d="M6 4 9 7 6 10" stroke="#04112b" stroke-width="1.8" fill="none"/></svg>Environmentally Friendly</div>
<div class="benefit" style="left:350px;top:2338px"><svg viewBox="0 0 14 14"><circle cx="7" cy="7" r="7" fill="#fff"/><path d="M6 4 9 7 6 10" stroke="#04112b" stroke-width="1.8" fill="none"/></svg>Wind Resistance</div>
<div class="btn" style="left:107px;top:2401px;width:168px;height:42px">LEARN MORE <svg viewBox="0 0 12 12"><circle cx="6" cy="6" r="6" fill="#fff"/><path d="M5 3.5 7.5 6 5 8.5" stroke="#0a7fd6" stroke-width="1.6" fill="none"/></svg></div>
<div class="photo" style="left:600px;top:1990px;width:493px;height:524px;background:linear-gradient(160deg,#9a9aa0 0%,#2b3a52 30%,#1d2a40 65%,#33455f 100%)" role="img" aria-label="Worker fastening dark metal roof tiles with a drill"></div>
<div class="stat-box" style="left:604px;top:2293px;width:202px;height:217px">
  <div style="margin-top:26px;font-family:'Open Sans',Arial,sans-serif;font-weight:600;font-size:46px">$0</div>
  <div style="font-size:15px;font-weight:700;line-height:30px;margin-top:4px">ROOF REPLACEMENT<br>ALTERNATIVE WITH<br>DOWN FINANCING</div>
</div>

<!-- Testimonials -->
<h2 class="section-title" style="left:0;width:1200px;text-align:center;top:2620px">Our Testimonials</h2>
<svg class="arrow" style="left:67px;top:2853px" viewBox="0 0 20 20"><path d="M13 3 6 10l7 7" stroke="#fff" stroke-width="2.2" fill="none"/></svg>
<svg class="arrow" style="left:1111px;top:2853px" viewBox="0 0 20 20"><path d="M7 3l7 7-7 7" stroke="#fff" stroke-width="2.2" fill="none"/></svg>
<article class="testimonial" style="left:116px"><div class="avatar" role="img" aria-label="Customer portrait"></div><div class="name">Elias</div><div class="stars">★★★★★</div><p>Can't believe how sturdy this stuff makes roofing shingles. You have to see it to believe it. Plus, they look great, too! Just like new.</p></article>
<article class="testimonial" style="left:463px"><div class="avatar" role="img" aria-label="Customer portrait"></div><div class="name">Tobin</div><div class="stars">★★★★★</div><p>Can't believe how sturdy this stuff makes roofing shingles. You have to see it to believe it. Plus, they look great, too! Just like new.</p></article>
<article class="testimonial" style="left:809px"><div class="avatar" role="img" aria-label="Customer portrait"></div><div class="name" style="left:92px">Delphine</div><div class="stars" style="left:174px">★★★★★</div><p>Can't believe how sturdy this stuff makes roofing shingles. You have to see it to believe it. Plus, they look great, too! Just like new.</p></article>

<!-- Performance tests -->
<h2 class="section-title" style="left:0;width:1200px;text-align:center;top:3118px">Perfomance Test</h2>
<div class="abs" style="left:0;width:1200px;text-align:center;top:3210px;font-size:13px;letter-spacing:.2px">PERFORMANCE TESTS: TIDEWELL PROTECTS AGAINST THE ELEMENTS</div>
<div class="tab" style="left:32px;width:168px">ICE BALL TEST</div>
<div class="tab" style="left:224px;width:172px">IMPACT TEST</div>
<div class="tab" style="left:417px;width:172px">STEEL BALL TEST</div>
<div class="tab active" style="left:611px;width:172px">ENVIRONMENTALTEST</div>
<div class="tab" style="left:806px;width:170px">HEAT TEST</div>
<div class="tab" style="left:998px;width:170px">HOT TIRE TEST</div>
<div class="photo" style="left:116px;top:3366px;width:968px;height:419px;border-radius:18px;border:2px solid #d7dde7;background:linear-gradient(120deg,#f0c78a 0%,#e7e4dc 30%,#b8bcc0 55%,#5b6b5a 100%)" role="img" aria-label="Worker on a ladder cleaning a roof gutter"></div>
<div class="abs heading" style="left:836px;top:3692px;font-size:22px;font-weight:600;color:#0b1f3f">PLAY NOW</div>
<svg class="abs" style="left:982px;top:3671px" width="66" height="66" viewBox="0 0 66 66"><circle cx="33" cy="33" r="33" fill="#fff"/><path d="M27 22v22l17-11z" fill="#0b1530"/></svg>

<!-- Form -->
<h2 class="section-title" style="left:0;width:1200px;text-align:center;top:3884px">Protect Your Roof</h2>
<form>
<div class="field" style="left:75px;top:3990px;width:342px">NAME</div>
<div class="field" style="left:428px;top:3990px;width:342px">EMAIL</div>
<div class="field" style="left:781px;top:3990px;width:342px">PHONE</div>
<div class="field" style="left:75px;top:4069px;width:342px">ADDRESS</div>
<div class="field" style="left:428px;top:4069px;width:342px">CITY</div>
<div class="field" style="left:781px;top:4069px;width:342px">STATE</div>
<div class="field" style="left:75px;top:4146px;width:342px">PROJECT</div>
<div class="field" style="left:428px;top:4146px;width:695px">MESSAGE</div>
</form>
<div class="btn" style="left:516px;top:4239px;width:168px;height:41px">SUBMIT <svg viewBox="0 0 12 12"><circle cx="6" cy="6" r="6" fill="#fff"/><path d="M5 3.5 7.5 6 5 8.5" stroke="#0a7fd6" stroke-width="1.6" fill="none"/></svg></div>

<!-- Footer -->
<svg class="abs" style="left:0;top:4350px" width="1200" height="100" viewBox="0 0 1200 100">
  <polygon points="150,92 594,12 1110,92 594,22" fill="#ffffff"/>
</svg>
<div class="logo" style="left:112px;top:4510px;font-size:20px"><i></i>Tidewell Sealer</div>
<svg class="abs" style="left:113px;top:4577px" width="14" height="16" viewBox="0 0 14 16"><path d="M7 0a6 6 0 0 0-6 6c0 4.5 6 10 6 10s6-5.5 6-10a6 6 0 0 0-6-6zm0 8.3A2.3 2.3 0 1 1 7 3.7a2.3 2.3 0 0 1 0 4.6z" fill="#fff"/></svg>
<div class="foot-link" style="left:140px;top:4576px;line-height:26px;color:#fff">2240 Harbor Point Road, Suite 210<br>Coral Bend, Florida 33901<br>United States</div>
<svg class="abs" style="left:113px;top:4660px" width="14" height="14" viewBox="0 0 14 14"><path d="M3 0 5.5 3 4 5c1 2 3 4 5 5l2-1.5 3 2.5-2 3C6 13.5.5 8 0 2z" fill="#fff"/></svg>
<div class="foot-link" style="left:140px;top:4659px;color:#fff">(800) 555-0142</div>

<div class="foot-head" style="left:437px">SEALERS</div>
<div class="foot-link" style="left:437px;top:4543px">Roof Sealers</div>
<div class="foot-link" style="left:437px;top:4575px">Roof Coatings</div>
<div class="foot-link" style="left:437px;top:4606px">Energy Efficient Roof</div>
<div class="foot-link" style="left:437px;top:4638px">Roof Facts</div>

<div class="foot-head" style="left:620px">ROOFS</div>
<div class="foot-link" style="left:620px;top:4543px">Roof Repair</div>
<div class="foot-link" style="left:620px;top:4575px">Roof Leaks</div>
<div class="foot-link" style="left:620px;top:4606px">Alternatives to Reroofing</div>
<div class="foot-link" style="left:620px;top:4638px">Roof Restoration</div>

<div class="foot-head" style="left:843px">TIDEWELL</div>
<div class="foot-link" style="left:843px;top:4543px">See us In Action</div>
<div class="foot-link" style="left:843px;top:4575px">FAQ</div>
<div class="foot-link" style="left:843px;top:4606px">Test Videos</div>
<div class="foot-link" style="left:843px;top:4638px">Video Gallery</div>

<div class="foot-head" style="left:1020px">COMPANY</div>
<div class="foot-link" style="left:1020px;top:4543px">About</div>
<div class="foot-link" style="left:1020px;top:4575px">Reviews</div>
<div class="foot-link" style="left:1020px;top:4606px">Contact</div>

<div class="abs" style="left:0;width:1200px;text-align:center;top:4701px;font-size:12px">Copyright@2024 - All Rights reserved By Tidewell Sealer</div>
<div class="social" style="left:536px" aria-label="Social link"></div>
<div class="social" style="left:583px" aria-label="Social link"></div>
<div class="social" style="left:630px" aria-label="Social link"></div>

</body>
</html>
```